Varnik Holdings — Business Card Design Brief
Overview
Design a double-sided business card for Varnik Holdings that highlights our two service arms: Varnik Communications (telecommunications) and Varnik Energy (business energy solutions). The card should feel smart and stand out when handed to clients.

Objectives
Showcase our areas of specialty clearly.
Reflect the overall Varnik / Varnik Holdings brand while acknowledging both arms.
Explore using both logos (Communications + Energy) or one unified logo, depending on the design.

Deliverables
One double-sided business card design (front + back).

Content & Copy
Front (preferred): Logo: Varnik / Varnik Holdings
Descriptor: Business Communications | Business Energy
Back:My contact details and company details
Core products: Business Mobile • Telephony • Internet • Business Energy Solutions

Brand & Visual Direction
We have a group logo currently tailored more toward telecoms, plus a separate Varnik Energy logo.
Please explore layouts that use both logos or just one, whichever works best.
Color: I wouldn't mind seeing an option using our the Blue/Purple gradient from our website (varnik-example.co.uk), but also open to non-gradient approaches and other colours..

Overall look: Smart, modern, and distinctive.
Format & Print Specs
Double-sided business card format. (Use a standard size

Must-Haves
Front: Varnik wording or Varnik Holdings wording with atleast 1 logo also on front “Business Communications | Business Energy.”

Back: Contact + company details and core products.
A design that stands out while remaining professional.

Nice-to-Have Options
A gradient version using our site’s Blue/Purple gradient.
A non-gradient version.
A dual-logo treatment versus a single-logo treatment.

Thanks
Owen

```html
<!DOCTYPE html>
<html lang="en">
<head>
<meta charset="utf-8">
<title>Varnik Holdings — Business Card</title>
<link href="https://fonts.googleapis.com/css2?family=Montserrat:wght@400;500;600;800;900&display=swap" rel="stylesheet">
<style>
  :root {
    --bg: #e6e6ea;
    --purple: #8b3fa3;
    --indigo: #5a5aa8;
    --blue: #1767a8;
    --navy: #221f6e;
    --cyan: #23a8e0;
    --comm-blue: #2d79c7;
    --lime: #c5d629;
    --green: #4bb748;
    --ink: #2a2a3a;
    --white: #ffffff;
  }
  * { box-sizing: border-box; margin: 0; padding: 0; }
  html, body { width: 1200px; height: 875px; overflow: hidden; }
  body {
    background: var(--bg);
    font-family: "Montserrat", Arial, sans-serif;
    display: flex; flex-direction: column; align-items: center; justify-content: center;
    gap: 32px;
  }
  .card {
    width: 680px; height: 388px; position: relative; overflow: hidden;
    box-shadow: 0 6px 18px rgba(0,0,0,.18);
  }

  /* Front */
  .card-front {
    background: linear-gradient(125deg, var(--purple) 0%, var(--indigo) 45%, var(--blue) 100%);
  }
  .front-marks {
    position: absolute; left: 0; right: 0; top: 110px;
    display: flex; align-items: center; justify-content: center; gap: 46px;
  }
  .brand-mark { display: flex; align-items: center; gap: 12px; font-weight: 600; font-size: 22px; }
  .brand-mark .dot { width: 30px; height: 30px; border-radius: 50%; flex: none; }
  .brand-mark.comm { color: var(--cyan); }
  .brand-mark.comm .dot { background: var(--cyan); }
  .brand-mark.energy { color: var(--lime); }
  .brand-mark.energy .dot { background: var(--lime); }
  .front-divider { width: 1px; height: 92px; background: var(--lime); opacity: .8; }
  .front-descriptor {
    position: absolute; left: 0; right: 0; bottom: 92px; text-align: center;
    font-size: 19px; font-weight: 500; letter-spacing: .3px;
  }
  .front-descriptor .comm { color: var(--cyan); }
  .front-descriptor .sep { color: var(--lime); margin: 0 6px; }
  .front-descriptor .energy { color: var(--lime); }

  /* Back */
  .card-back { background: var(--white); }
  .wordmark {
    position: absolute; left: 44px; top: 62px;
    font-weight: 900; font-size: 64px; letter-spacing: 1px; color: var(--navy);
  }
  .contact { position: absolute; left: 44px; top: 152px; }
  .contact-accent {
    position: absolute; left: 0; top: 4px; width: 12px; height: 44px;
    background: linear-gradient(180deg, var(--cyan), var(--comm-blue));
  }
  .person { padding-left: 22px; }
  .person-name { font-weight: 800; font-size: 22px; color: var(--navy); letter-spacing: .5px; }
  .person-role { font-size: 15px; color: var(--ink); margin-top: 2px; }
  .address { margin-top: 16px; padding-left: 22px; font-size: 14px; line-height: 1.45; color: var(--ink); }
  .contact-list { list-style: none; margin-top: 10px; padding-left: 22px; font-size: 14px; line-height: 1.6; color: var(--ink); }
  .contact-list li { display: flex; align-items: center; gap: 8px; }
  .contact-list svg { width: 13px; height: 13px; flex: none; }
  .back-marks {
    position: absolute; right: 44px; top: 70px;
    display: flex; flex-direction: column; align-items: flex-start; gap: 46px;
  }
  .back-marks .brand-mark.comm { color: var(--comm-blue); }
  .back-marks .brand-mark.comm .dot { background: var(--comm-blue); }
  .back-marks .brand-mark.energy { color: var(--green); margin-left: 40px; }
  .back-marks .brand-mark.energy .dot { background: var(--green); }
  .product-band {
    position: absolute; left: 0; right: 0; bottom: 0; height: 40px;
    background: var(--navy); color: var(--white);
    display: flex; align-items: center; justify-content: center; gap: 10px;
    font-size: 15px; font-weight: 500; letter-spacing: .3px;
  }
  .product-band .bullet { color: var(--cyan); }
</style>
</head>
<body>

<section class="card card-front" aria-label="Card front">
  <div class="front-marks">
    <div class="brand-mark comm"><span class="dot"></span>Varnik Communications</div>
    <div class="front-divider"></div>
    <div class="brand-mark energy"><span class="dot"></span>Varnik Energy</div>
  </div>
  <p class="front-descriptor">
    <span class="comm">Business Communications</span><span class="sep">|</span><span class="energy">Business Energy</span>
  </p>
</section>

<section class="card card-back" aria-label="Card back">
  <h1 class="wordmark">VARNIK</h1>

  <div class="contact">
    <span class="contact-accent"></span>
    <div class="person">
      <p class="person-name">DANIEL HARTLEY</p>
      <p class="person-role">Founder/CEO</p>
    </div>
    <p class="address">24 Calder Row, Ashbridge<br>England, AB7 2XQ</p>
    <ul class="contact-list">
      <li>
        <svg viewBox="0 0 16 16" aria-hidden="true"><path fill="#23a8e0" d="M3.5 1.5l2.5 2.8-1.4 1.7c.9 1.9 2.3 3.4 4.3 4.4l1.7-1.4 2.9 2.4-1.3 2.4C6.8 13.4 2.4 8.9 1.2 3z"/></svg>
        +44 0100 555 0142
      </li>
      <li>
        <svg viewBox="0 0 16 16" aria-hidden="true"><rect x="1" y="3" width="14" height="10" rx="1" fill="#23a8e0"/><path d="M1.5 3.5L8 9l6.5-5.5" stroke="#fff" stroke-width="1.4" fill="none"/></svg>
        info@varnik-example.co.uk
      </li>
      <li>
        <svg viewBox="0 0 16 16" aria-hidden="true"><circle cx="8" cy="8" r="7" fill="#23a8e0"/><path d="M1 8h14M8 1c-3 3.5-3 10.5 0 14M8 1c3 3.5 3 10.5 0 14" stroke="#fff" stroke-width="1" fill="none"/></svg>
        www.varnik-example.co.uk
      </li>
    </ul>
  </div>

  <div class="back-marks">
    <div class="brand-mark comm"><span class="dot"></span>Varnik Communications</div>
    <div class="brand-mark energy"><span class="dot"></span>Varnik Energy</div>
  </div>

  <div class="product-band">
    <span>Business Mobile</span><span class="bullet">•</span>
    <span>Telephony</span><span class="bullet">•</span>
    <span>Internet</span><span class="bullet">•</span>
    <span>Business Energy Solutions</span>
  </div>
</section>

</body>
</html>
```